BrivoTerna. Lantern of the Steady Harvest. Business card

Professional business card for BrivoTerna (Lantern of the Steady Harvest)
My rationale: Strategy-> Execution-> Results-> Value that lead to the BrivoTerna name: We put the Lantern of the Steady Harvest.
We deliver value to our customers helping them at defining a good strategy (cyan arrow). 90% of well formulated strategies fail due to poor execution so we also consider strategical execution very important (green arrow). Due to the execution we obtain the results (blue arrow). Finally, the results provide feedback to redefine strategy, and the new strategy has to be executed and new results obtained providing new feedback and on and on. It's like a wheel that finally, must create corporate value: value for shareholders, staholders, employees, providers...-

Target Market(s)

CEOs and steering comitees , invewrnent funds

Industry/Entity Type

Business Consultant

Contact Information for Business Card

Teodoro Vinsquel
CEO & Founder
teodoro.vinsquel@brivoterna-example.com
Mobile: +34 655.803.912
www.brivoterna-example.com

Colors

Designer to choose colors to be used in the design.

Requirements
Nice to have
• Nice to hace the words: Strategy, execution, results
• Nice to vave the claim: Lantern of the Steady Harvest
• The three colors should be shown:
• cyan for STRATEGY
• green for EXECUTION
• blue for RESULTS
Should not have
• Complete black background

```html
<!DOCTYPE html>
<html lang="en">
<head>
<meta charset="utf-8">
<title>BrivoTerna — Business Card</title>
<link href="https://fonts.googleapis.com/css2?family=Source+Sans+3:wght@400;700&display=swap" rel="stylesheet">
<style>
  :root {
    --backdrop: #e4e6e8;
    --card: #fafafa;
    --brand-blue: #0b3a9c;
    --text-grey: #4a4a4a;
    --silver-light: #eef0f2;
    --silver-dark: #cfd3d8;
  }
  html, body {
    margin: 0;
    padding: 0;
    width: 1200px;
    height: 1077px;
    overflow: hidden;
    background: var(--backdrop);
    font-family: "Source Sans 3", "Myriad Pro", sans-serif;
  }
  .business-card {
    position: absolute;
    left: 150px;
    top: 280px;
    width: 900px;
    height: 517px;
    background: var(--card);
    border-radius: 28px;
    box-shadow: 0 10px 30px rgba(0, 0, 0, 0.12);
    overflow: hidden;
  }
  .brand-name {
    position: absolute;
    left: 50px;
    top: 40px;
    margin: 0;
    font-size: 86px;
    font-weight: 700;
    letter-spacing: -3px;
    line-height: 1;
    color: var(--brand-blue);
  }
  .symbol-placeholder {
    position: absolute;
    left: 560px;
    top: 80px;
    width: 300px;
    height: 355px;
    border-radius: 40px;
    background: radial-gradient(ellipse at 60% 50%, var(--silver-dark) 0%, var(--silver-light) 60%, var(--card) 100%);
    opacity: 0.8;
  }
  .person {
    position: absolute;
    left: 50px;
    top: 278px;
  }
  .person-name {
    margin: 0;
    font-size: 29px;
    font-weight: 700;
    color: var(--brand-blue);
    line-height: 1.2;
  }
  .person-role {
    margin: 2px 0 0;
    font-size: 24px;
    font-weight: 400;
    color: var(--text-grey);
    line-height: 1.2;
  }
  .contact-list {
    position: absolute;
    left: 50px;
    top: 384px;
    margin: 0;
    padding: 0;
    list-style: none;
  }
  .contact-item {
    display: flex;
    align-items: center;
    height: 35px;
    font-size: 22px;
    color: var(--text-grey);
  }
  .contact-icon {
    width: 20px;
    height: 20px;
    margin-right: 12px;
    fill: none;
    stroke: var(--brand-blue);
    stroke-width: 2;
  }
</style>
</head>
<body>
  <main class="business-card">
    <h1 class="brand-name">BrivoTerna</h1>

    <div class="symbol-placeholder" role="img" aria-label="Faint silver brand symbol decoration"></div>

    <section class="person">
      <p class="person-name">Teodoro Vinsquel</p>
      <p class="person-role">CEO &amp; Founder</p>
    </section>

    <ul class="contact-list">
      <li class="contact-item">
        <svg class="contact-icon" viewBox="0 0 20 20" aria-hidden="true">
          <rect x="5" y="2" width="10" height="16" rx="1.5"/>
          <line x1="8.5" y1="15" x2="11.5" y2="15"/>
        </svg>
        +34 655.803.912
      </li>
      <li class="contact-item">
        <svg class="contact-icon" viewBox="0 0 20 20" aria-hidden="true">
          <rect x="2" y="5" width="16" height="11" rx="1"/>
          <polyline points="2,5 10,11 18,5"/>
        </svg>
        teodoro.vinsquel@brivoterna-example.com
      </li>
      <li class="contact-item">
        <svg class="contact-icon" viewBox="0 0 20 20" aria-hidden="true">
          <circle cx="10" cy="10" r="7.5"/>
          <ellipse cx="10" cy="10" rx="3.5" ry="7.5"/>
          <line x1="2.5" y1="10" x2="17.5" y2="10"/>
        </svg>
        www.brivoterna-example.com
      </li>
    </ul>
  </main>
</body>
</html>
```